Business Card for a New Zealand IT Startup

I need a business card for VELTA Holdings. We are a young startup based in New Zealand working in internet marketing and web development. The design should have some element connected to New Zealand, such as wave, koru or silver fern, just don't use a kiwi bird.

```html
<!DOCTYPE html>
<html lang="en">
<head>
<meta charset="utf-8">
<title>VELTA Holdings – Business Card</title>
<link href="https://fonts.googleapis.com/css2?family=Roboto:wght@400;500;700&display=swap" rel="stylesheet">
<style>
  :root {
    --brand-blue: #0a6fba;
    --brand-orange: #f15a24;
    --paper: #ffffff;
    --backdrop: #e9e6e1;
  }
  * { margin: 0; padding: 0; box-sizing: border-box; }
  html, body {
    width: 1125px; height: 1200px; overflow: hidden;
    background: var(--backdrop);
    font-family: "Roboto", Arial, sans-serif;
  }
  .sheet { position: relative; width: 1125px; height: 1200px; }
  .card {
    position: absolute; left: 150px; width: 826px; height: 470px;
    border-radius: 22px; overflow: hidden;
    box-shadow: 0 3px 8px rgba(0,0,0,0.25);
  }
  .card--front { top: 106px; background: var(--paper); }
  .card--back { top: 638px; background: var(--brand-blue); }

  .front-panel { position: absolute; inset: 0; width: 826px; height: 470px; }

  .wordmark {
    position: absolute; left: 74px; top: 158px; width: 330px;
    color: var(--brand-blue); font-weight: 700;
  }
  .wordmark__main { display: block; font-size: 96px; line-height: 0.9; letter-spacing: 2px; }
  .wordmark__sub { display: block; font-size: 27px; letter-spacing: 12px; margin-top: 14px; }

  .person { position: absolute; left: 517px; top: 58px; color: var(--paper); }
  .person__name { font-size: 30px; font-weight: 500; letter-spacing: 0.3px; line-height: 1.1; }
  .person__role { font-size: 20px; font-weight: 500; line-height: 1.1; }

  .address {
    position: absolute; right: 42px; top: 232px; text-align: right;
    color: var(--paper); font-size: 20px; line-height: 25px; font-style: normal;
  }
  .contacts {
    position: absolute; right: 42px; top: 292px; list-style: none;
    color: var(--paper); font-size: 20px;
  }
  .contacts li {
    display: flex; justify-content: flex-end; align-items: center;
    height: 26px; gap: 10px;
  }
  .contacts svg { width: 20px; height: 20px; flex: none; }

  .back-waves { position: absolute; inset: 0; width: 826px; height: 470px; }
  .back-name {
    position: absolute; left: 0; right: 0; top: 150px; text-align: center;
    color: var(--paper); font-weight: 700; font-size: 54px; letter-spacing: 4px;
  }
  .back-url {
    position: absolute; left: 0; right: 0; top: 388px; text-align: center;
    color: var(--paper); font-size: 20px; letter-spacing: 5.5px;
  }
  .back-url strong { font-weight: 500; }
</style>
</head>
<body>
<main class="sheet">
  <section class="card card--front" aria-label="Card front">
    <svg class="front-panel" viewBox="0 0 826 470" aria-hidden="true">
      <rect x="468" y="0" width="358" height="470" fill="var(--brand-blue)"/>
      <polygon points="468,0 826,0 826,118 468,226" fill="var(--brand-orange)"/>
      <line x1="468" y1="229" x2="826" y2="121" stroke="var(--paper)" stroke-width="5"/>
    </svg>

    <div class="wordmark">
      <span class="wordmark__main">VELTA</span>
      <span class="wordmark__sub">HOLDINGS</span>
    </div>

    <div class="person">
      <p class="person__name">MARK TAYLOR</p>
      <p class="person__role">CEO/FOUNDER</p>
    </div>

    <address class="address">
      4316 Kowhai Street<br>
      Wellington, Kapiti 60214
    </address>

    <ul class="contacts">
      <li>612 304 7719
        <svg viewBox="0 0 20 20" aria-label="Phone"><path fill="#fff" d="M5 2l3 4-2 2c1 2 3 4 5 5l2-2 4 3-2 3c-6 0-12-6-12-12z"/></svg>
      </li>
      <li>745 219 8036
        <svg viewBox="0 0 20 20" aria-label="Mobile"><rect x="5" y="1" width="10" height="18" rx="1.5" fill="none" stroke="#fff" stroke-width="2"/><circle cx="10" cy="16" r="1" fill="#fff"/></svg>
      </li>
      <li>391 572 4608
        <svg viewBox="0 0 20 20" aria-label="Fax"><rect x="5" y="2" width="10" height="6" fill="#fff"/><rect x="2" y="8" width="16" height="7" rx="1" fill="#fff"/><rect x="5" y="13" width="10" height="5" fill="#fff" stroke="var(--brand-blue)" stroke-width="1"/></svg>
      </li>
      <li>mark@veltaholdings.com
        <svg viewBox="0 0 20 20" aria-label="Email"><rect x="2" y="5" width="16" height="11" fill="#fff"/><path d="M2 5l8 6 8-6" fill="none" stroke="var(--brand-blue)" stroke-width="1.3"/></svg>
      </li>
      <li>www.veltaholdings.com
        <svg viewBox="0 0 20 20" aria-label="Website"><circle cx="10" cy="10" r="8" fill="#fff"/><path d="M6 6c2 0 3 1 2 3s-3 1-2 4M13 4c-1 2 1 3 2 3M12 16c0-2 2-3 3-2" fill="none" stroke="var(--brand-blue)" stroke-width="1.6"/></svg>
      </li>
    </ul>
  </section>

  <section class="card card--back" aria-label="Card back">
    <svg class="back-waves" viewBox="0 0 826 470" aria-hidden="true">
      <path d="M0 262 C 100 232, 200 232, 300 262 S 500 292, 600 262 S 760 232, 826 252" fill="none" stroke="var(--paper)" stroke-width="4" stroke-linecap="round" opacity="0.85"/>
      <path d="M0 290 C 100 260, 200 260, 300 290 S 500 320, 600 290 S 760 260, 826 280" fill="none" stroke="var(--paper)" stroke-width="3" stroke-linecap="round" opacity="0.45"/>
      <path d="M0 316 C 100 286, 200 286, 300 316 S 500 346, 600 316 S 760 286, 826 306" fill="none" stroke="var(--paper)" stroke-width="2" stroke-linecap="round" opacity="0.25"/>
    </svg>
    <p class="back-name">VELTA HOLDINGS</p>
    <p class="back-url">www.<strong>veltaholdings</strong>.com</p>
  </section>
</main>
</body>
</html>
```